BUSINESS CARD DESIGN

NAME- DALE VORSKIN
PHONE NUMER - 555- 714-9082
EMAIL- OFFICE@TRV-GROUNDMAKRZ.COM
BACK OF CARD- SPEACIALIZES IN LAND CLEARING, FORESTRY MUCLHING AND EXCAVATION

Contact Information for Business Card

NAME- DALE VORSKIN PHONE NUMER - 555- 714-9082 EMAIL- OFFICE@TRV-GROUNDMAKRZ.COM BACK OF CARD- SPEACIALIZES IN LAND CLEARING , MUCLHING AND EXCAVATION

```html
<!DOCTYPE html>
<html lang="en">
<head>
<meta charset="utf-8">
<title>Trevane Groundmakrz – Business Card</title>
<link rel="stylesheet" href="https://fonts.googleapis.com/css2?family=Roboto:wght@300;400;500;700&display=swap">
<style>
  :root {
    --page: #e4e7e8;
    --card: #222226;
    --card-deep: #18181b;
    --accent: #f7b21c;
    --ink-light: #e9e9ea;
  }
  * { box-sizing: border-box; margin: 0; padding: 0; }
  html, body { width: 1200px; height: 960px; overflow: hidden; }
  body {
    background: var(--page);
    font-family: "Roboto", sans-serif;
    position: relative;
  }
  .card {
    position: absolute;
    left: 252px;
    width: 700px;
    height: 400px;
    background: var(--card);
    border-radius: 28px;
    border-left: 4px solid var(--accent);
    border-bottom: 4px solid var(--accent);
    overflow: hidden;
  }
  .card--front { top: 60px; }
  .card--back { top: 500px; }

  /* front */
  .front-brand {
    position: absolute;
    left: 0; right: 0; top: 110px;
    display: flex; flex-direction: column; align-items: center; gap: 14px;
  }
  .front-brand__mark {
    width: 120px; height: 120px; border-radius: 50%;
    background: var(--card-deep);
  }
  .front-brand__name {
    font-weight: 700; font-size: 26px; letter-spacing: 2px;
    color: var(--card-deep); text-align: center;
  }
  .tagline {
    position: absolute; left: 0; right: 0; top: 356px;
    text-align: center; color: var(--accent);
    font-size: 15.5px; letter-spacing: 0.6px;
  }

  /* back */
  .back-brand {
    position: absolute; left: 24px; top: 80px; width: 300px;
    display: flex; flex-direction: column; align-items: center; gap: 12px;
  }
  .back-brand__mark {
    width: 150px; height: 150px; border-radius: 50%;
    background: var(--accent);
  }
  .back-brand__name {
    color: var(--accent); font-weight: 700; text-align: center;
    font-size: 21px; line-height: 1.25; letter-spacing: 1.5px;
  }
  .person-name {
    position: absolute; right: 70px; top: 50px;
    font-size: 37px; color: var(--accent); letter-spacing: 1px;
    font-weight: 300;
  }
  .person-name__first { font-weight: 700; }
  .contact-list {
    position: absolute; right: 70px; top: 278px;
    list-style: none; text-align: right;
    color: var(--ink-light); font-size: 15px; letter-spacing: 0.8px;
  }
  .contact-list li { height: 28.5px; line-height: 28px; }
  .rail { position: absolute; left: 0; top: 0; }
</style>
</head>
<body>

<section class="card card--front">
  <div class="front-brand">
    <div class="front-brand__mark"></div>
    <div class="front-brand__name">TREVANE GROUNDMAKRZ LLC</div>
  </div>
  <p class="tagline">SPEACIALIZES IN LAND CLEARING , MUCLHING AND EXCAVATION</p>
</section>

<section class="card card--back">
  <div class="back-brand">
    <div class="back-brand__mark"></div>
    <div class="back-brand__name">TREVANE GROUNDMAKRZ LLC<br>555-714-9082</div>
  </div>

  <h1 class="person-name"><span class="person-name__first">DALE</span> VORSKIN</h1>

  <svg class="rail" width="700" height="400" viewBox="0 0 700 400" aria-hidden="true">
    <line x1="651" y1="26" x2="651" y2="377" stroke="#f7b21c" stroke-width="2"/>
    <!-- person badge -->
    <polygon points="651,49 675,73 651,97 627,73" fill="#f7b21c"/>
    <circle cx="651" cy="66" r="5" fill="#222226"/>
    <path d="M640 84 q0-10 11-10 q11 0 11 10 z" fill="#222226"/>
    <!-- phone -->
    <polygon points="651,276 665,290 651,304 637,290" fill="#f7b21c"/>
    <path d="M646 284 l3 0 l1 3 l-2 1 q1 3 4 4 l1-2 l3 1 l0 3 q-9 0-10-10z" fill="#222226"/>
    <!-- web -->
    <polygon points="651,305 665,319 651,333 637,319" fill="#f7b21c"/>
    <circle cx="651" cy="319" r="5.5" fill="none" stroke="#222226" stroke-width="1.5"/>
    <line x1="645.5" y1="319" x2="656.5" y2="319" stroke="#222226" stroke-width="1.2"/>
    <!-- mail -->
    <polygon points="651,334 665,348 651,362 637,348" fill="#f7b21c"/>
    <rect x="645" y="344" width="12" height="8" fill="none" stroke="#222226" stroke-width="1.4"/>
    <path d="M645 344 l6 5 l6 -5" fill="none" stroke="#222226" stroke-width="1.2"/>
  </svg>

  <ul class="contact-list">
    <li>555- 714-9082</li>
    <li>WWW.TRV-GROUNDMAKRZ.COM</li>
    <li>OFFICE@TRV-GROUNDMAKRZ.COM</li>
  </ul>
</section>

</body>
</html>
```